New Business Card Design Project

Need a design that will create an impact / strong impression towards our clients for our business. We are in the lighting business and we do lighting retrofits for large commercial to industrial clientele.

Target Market(s)

Lighting Industry

Industry/Entity Type

Business

Font styles to use
Other font styles liked:
• we would like to use the font on our logo, not sure what it is though..

Requirements
Must have
• Our logo.
Nice to have
• We are open to suggestions that have to do with lighting.

```html
<!DOCTYPE html>
<html lang="en">
<head>
<meta charset="utf-8">
<title>Lumenforge Retrofit Group — Business Card</title>
<link rel="stylesheet" href="https://fonts.googleapis.com/css2?family=Montserrat:wght@400;500;600;700&family=Oswald:wght@600&display=swap">
<style>
  :root {
    --backdrop: #141414;
    --card: #1e1e1e;
    --card-edge: #262626;
    --green: #1f8f45;
    --green-light: #5cc164;
    --white: #f2f2f2;
    --grey: #7a7a7a;
  }
  * { box-sizing: border-box; margin: 0; padding: 0; }
  html, body {
    width: 1200px; height: 900px; overflow: hidden;
    background: radial-gradient(ellipse at 60% 40%, #2a2a2a 0%, var(--backdrop) 70%);
    font-family: "Montserrat", sans-serif;
  }
  .card {
    position: absolute; left: 280px; width: 640px; height: 366px;
    background: linear-gradient(135deg, var(--card) 0%, var(--card-edge) 100%);
    box-shadow: 0 18px 40px rgba(0,0,0,.6);
  }
  .card--front { top: 60px; }
  .card--back { top: 474px; }

  /* front */
  .brand {
    position: absolute; top: 128px; left: 0; right: 0;
    display: flex; justify-content: center; align-items: center; gap: 14px;
  }
  .brand__mark { width: 22px; height: 22px; background: var(--green); }
  .brand__name {
    font-weight: 700; font-size: 30px; letter-spacing: 2px;
    color: var(--white); text-transform: uppercase;
  }
  .brand__tagline {
    position: absolute; top: 178px; left: 0; right: 0; text-align: center;
    font-size: 11px; font-weight: 600; letter-spacing: 3px; color: var(--white);
    text-transform: uppercase;
  }
  .front__web {
    position: absolute; bottom: 48px; left: 0; right: 0; text-align: center;
    font-size: 13px; letter-spacing: 2px; color: var(--white);
  }
  .front__web span { color: var(--green-light); }

  /* back */
  .person {
    position: absolute; top: 116px; left: 100px; width: 200px; text-align: right;
  }
  .person__name {
    font-family: "Oswald", sans-serif; font-weight: 600; font-size: 36px;
    line-height: 1; color: var(--green); text-transform: uppercase; letter-spacing: 1px;
  }
  .person__role { font-size: 17px; color: var(--grey); margin-top: 4px; }
  .divider {
    position: absolute; top: 118px; left: 318px; width: 1px; height: 72px;
    background: var(--green);
  }
  .contacts {
    position: absolute; top: 124px; left: 340px; list-style: none;
  }
  .contacts li {
    display: flex; align-items: center; gap: 12px;
    font-size: 14px; color: var(--white); letter-spacing: .5px; height: 22px;
  }
  .contacts svg { width: 12px; height: 12px; fill: var(--green); flex: none; }
  .location {
    position: absolute; bottom: 50px; left: 70px;
    font-size: 15px; color: var(--white); letter-spacing: .5px;
  }
  .location__label { color: var(--green-light); }
</style>
</head>
<body>
  <section class="card card--front">
    <div class="brand">
      <span class="brand__mark"></span>
      <span class="brand__name">Lumenforge</span>
    </div>
    <p class="brand__tagline">Lumenforge Retrofit Group, LLC.</p>
    <p class="front__web">www.<span>lumenforgegroup</span>.com</p>
  </section>

  <section class="card card--back">
    <div class="person">
      <h1 class="person__name">Daniel Reyes</h1>
      <p class="person__role">Founder</p>
    </div>
    <div class="divider"></div>
    <ul class="contacts">
      <li>
        <svg viewBox="0 0 24 24" aria-hidden="true"><path d="M6.6 10.8a15 15 0 0 0 6.6 6.6l2.2-2.2a1 1 0 0 1 1-.25 11.4 11.4 0 0 0 3.6.6 1 1 0 0 1 1 1V20a1 1 0 0 1-1 1A17 17 0 0 1 3 4a1 1 0 0 1 1-1h3.5a1 1 0 0 1 1 1c0 1.25.2 2.45.6 3.6a1 1 0 0 1-.25 1z"/></svg>
        0400 555 019
      </li>
      <li>
        <svg viewBox="0 0 24 24" aria-hidden="true"><path d="M2 5h20v14H2z M2 5l10 8 10-8" /></svg>
        info@lumenforgegroup.com
      </li>
      <li>
        <svg viewBox="0 0 24 24" aria-hidden="true"><circle cx="12" cy="12" r="10"/></svg>
        www.lumenforgegroup.com
      </li>
    </ul>
    <p class="location"><span class="location__label">Location:</span> 4870 Harbor Lane, Suite Tempe 85281</p>
  </section>
</body>
</html>
```